New Business Cards for Tormin Group

We need a new Business Card to compliment our new logo. We are a vibrant design, manufacture and install business providing recreation areas, public parks and Municipal spaces. We want business cards that are classy, modern and clean.

We have recently changed our logo, and are celebrating our 40th anniversary. We want business cards with a new modern design to reflect our status.

Target Market(s)

Customers

Contact Information for Business Card

We need all the details of our 3 offices as per the business card attached. Please disregard the old logo on the business card, the other three files show our new logo.

Requirements
Must have
• All info as per attached business card but with new logo.
Nice to have

```html
<!DOCTYPE html>
<html lang="en">
<head>
<meta charset="utf-8">
<title>Tormin Group Business Card</title>
<link rel="stylesheet" href="https://fonts.googleapis.com/css2?family=Lato:wght@400;700&display=swap">
<style>
  :root {
    --backdrop: #5e5e5e;
    --card: #ffffff;
    --brand-red: #ec2d37;
    --charcoal: #3f3f41;
    --text-dark: #333333;
    --text-muted: #555555;
    --rule: #8a8a8a;
  }
  html, body {
    margin: 0;
    width: 1200px;
    height: 1200px;
    overflow: hidden;
    background: var(--backdrop);
    font-family: "Lato", Arial, sans-serif;
  }
  .card {
    position: absolute;
    left: 60px;
    top: 285px;
    width: 846px;
    height: 493px;
    background: var(--card);
    transform: scale(1.2766);
    transform-origin: 0 0;
    box-shadow: 0 3px 10px rgba(0,0,0,0.35);
    overflow: hidden;
  }
  .card > * { position: absolute; margin: 0; }
  .name-accent { left: 0; top: 70px; width: 7px; height: 58px; background: var(--brand-red); }
  .person-name { left: 32px; top: 64px; font-size: 28px; font-weight: 400; color: var(--brand-red); line-height: 1.1; }
  .person-title { left: 32px; top: 106px; font-size: 18.5px; color: var(--text-dark); line-height: 1.1; }
  .brand { right: 32px; top: 72px; display: flex; align-items: center; gap: 10px; }
  .brand-dot { width: 44px; height: 44px; border-radius: 50%; background: var(--brand-red); }
  .brand-name { font-size: 30px; font-weight: 700; color: var(--charcoal); letter-spacing: 0.5px; }
  .direct { left: 32px; font-size: 15px; font-weight: 700; color: var(--text-dark); }
  .direct.phone { top: 216px; }
  .direct.email { top: 253px; }
  .divider { left: 32px; top: 289px; width: 781px; height: 1px; background: var(--rule); }
  .office { top: 304px; }
  .office-head { font-size: 20px; color: var(--brand-red); margin: 0 0 9px; font-weight: 400; }
  .office-line { font-size: 15.2px; color: var(--text-muted); margin: 0; line-height: 25.3px; white-space: nowrap; }
  .office.head-office { left: 32px; }
  .office.dubai { left: 333px; }
  .office.qatar { left: 597px; top: 307px; }
  .band-red { left: 0; top: 450px; width: 563px; height: 31px; background: var(--brand-red); }
  .band-web { left: 566px; top: 450px; width: 264px; height: 31px; background: var(--charcoal); color: #fff; font-size: 15px; line-height: 31px; padding-left: 31px; box-sizing: border-box; }
  .band-end { left: 833px; top: 450px; width: 13px; height: 31px; background: var(--brand-red); }
</style>
</head>
<body>
  <div class="card">
    <div class="name-accent"></div>
    <h1 class="person-name">Rami Tasouli</h1>
    <p class="person-title">Managing Partner</p>

    <div class="brand">
      <span class="brand-dot"></span>
      <span class="brand-name">TORMIN GROUP</span>
    </div>

    <p class="direct phone">Phone: +971 (0)50 318 7426</p>
    <p class="direct email">Email: rami@tormingroup.com</p>

    <div class="divider"></div>

    <div class="office head-office">
      <h2 class="office-head">Head Office</h2>
      <p class="office-line">P.O. Box: 41820 Abu Dhabi. U.A.E</p>
      <p class="office-line">Tel No: +971 (0)2 5127390</p>
      <p class="office-line">Fax No: +971(0)2 5127391</p>
      <p class="office-line">Email: sales@tormingroup.com</p>
    </div>

    <div class="office dubai">
      <h2 class="office-head">Dubai Office</h2>
      <p class="office-line">P.O. Box: 582144 Dubai, U.A.E</p>
      <p class="office-line">Tel No: +971 (0)4 736208</p>
      <p class="office-line">Fax No: +971(0)4 736215</p>
      <p class="office-line">Email: sales@tormingroup.com</p>
    </div>

    <div class="office qatar">
      <h2 class="office-head">Qater Office</h2>
      <p class="office-line">P.O. Box: 20973 Doha, Qatter</p>
      <p class="office-line">Tel No: +974 41857326</p>
      <p class="office-line">Fax No: +971 41857390</p>
      <p class="office-line">Email: sales@tormingroup.com</p>
    </div>

    <div class="band-red"></div>
    <div class="band-web">www.tormingroup.com</div>
    <div class="band-end"></div>
  </div>
</body>
</html>
```